Personal Chef Needs a Good Web Design

Hi everyone!
My name is Leo, I work as a private chef for last 10 years, traveling all around the world and cooking in private megayacht and villas.
I'm about to settle down in my hometown in Europe for a while. And therefore I need a website that will show my story, pics and recipes, nutritional advices and of course offer a Personal and Private Chef services( working for 4-5 families and bringing delicious food to their house).
My clients are extremely rich folks, but usually are down to earth ones.
I believe, the web site should be focused on attention to:
-VIP person's wife( as she is usually responsible for food for family) and be simple.
-to famous people agents and be on high level.

There will be about 10 different menus and 6 different service offers

--UPDATE--
Logo Design:
+My thoughts are- printed structure of the vegetable or fruit on a white font. Like you slice the buffalo tomato, put it in red paint and print it on the edge of the page. See attached files named logo. Can be any nice structured thing, like tomato, lemon, red cabbage etc.
+Classic logos with chef's hat or knives are good too.
+Need to have the space for me to add the name( the fonts can be provided)

Target Market(s)

Private person. 80% Russian clients.

Industry/Entity Type

Cooking

Coding

Coded - Design and coding required

Number of Pages Required

3 page

Requirements
Must have
• Contact form/ Request back call/ Schedule a free consultation
Nice to have
• The client will need to choose straight ahead from the range of services I offer, like:
• -Private Chef( cooking only for the client)
• -Personal Chef( cooking for around 5 clients, bringing the ready to be heated food to their door)
• -Romantic dinner for two
• -Professional Sommelier service
• -Build your kitchen( offering design, equipment and that will fit your requirements)
• -Other( flowers, waiters, barista, equipment rental)
• So this column should go right after the introduction/aboutme part and will lead to separate pages with how-it-works thing for each.

```html
<!DOCTYPE html>
<html lang="en">
<head>
<meta charset="utf-8">
<title>Leo Chef — Private Chef</title>
<link rel="stylesheet" href="https://fonts.googleapis.com/css2?family=Sorts+Mill+Goudy&family=Open+Sans:wght@400;600;700&display=swap">
<style>
  :root {
    --accent: #f4460f;
    --ink: #111111;
    --black: #0b0b0b;
    --white: #ffffff;
    --grey-text: #6b6b6b;
    --line: #d5d5d5;
    --map: #e2e2e2;
    --band: #1f1c1c;
  }
  * { box-sizing: border-box; margin: 0; padding: 0; }
  html, body { width: 1200px; height: 2571px; overflow: hidden; background: var(--white); }
  body { position: relative; font-family: "Open Sans", Arial, sans-serif; color: var(--ink); }
  .abs { position: absolute; }
  .serif { font-family: "Sorts Mill Goudy", Georgia, serif; }

  /* Hero */
  .hero { left: 0; top: 0; width: 1200px; height: 576px;
    background: linear-gradient(100deg, #cfcac6 0%, #a9a29d 30%, #8d8580 55%, #7d746e 75%, #a55a45 100%); }
  .hero::after { content: ""; position: absolute; inset: 0; background: rgba(40,35,32,0.28); }
  .menu-toggle { right: 160px; top: 14px; width: 22px; z-index: 2; }
  .menu-toggle span { display: block; height: 3px; background: var(--white); margin-bottom: 4px; }
  .slide-arrow { top: 255px; width: 48px; height: 48px; border: 2px solid rgba(255,255,255,0.8); border-radius: 50%; z-index: 2; }
  .slide-arrow svg { position: absolute; left: 16px; top: 15px; }
  .brand { left: 0; top: 180px; width: 1200px; text-align: center; z-index: 2; color: var(--white);
    font-size: 96px; letter-spacing: 18px; line-height: 1; }
  .brand-sub { left: 0; top: 290px; width: 1200px; text-align: center; z-index: 2; color: var(--white);
    font-size: 28px; letter-spacing: 12px; }
  .hero-copy { left: 0; top: 398px; width: 1200px; text-align: center; z-index: 2; color: var(--white);
    font-size: 17px; line-height: 28px; }
  .btn-outline { left: 535px; top: 476px; width: 132px; height: 42px; border: 2px solid var(--white); border-radius: 21px;
    color: var(--white); font-weight: 700; font-size: 14px; text-align: center; line-height: 38px; z-index: 2; }

  /* Nav */
  .main-nav { top: 596px; font-size: 17px; color: var(--ink); }
  .nav-active-line { left: 377px; top: 633px; width: 72px; height: 2px; background: var(--accent); opacity: 0.6; }

  /* Intro */
  .intro-frame { left: 206px; top: 662px; width: 332px; height: 367px; border: 1px solid #cfcfcf; }
  .intro-photo { left: 219px; top: 675px; width: 336px; height: 374px;
    background: linear-gradient(160deg, #e9e4df 0%, #c9bdb2 40%, #6f5c48 70%, #2c2620 100%); }
  .intro-title { left: 600px; top: 732px; font-size: 34px; }
  .intro-text { left: 600px; top: 790px; width: 381px; font-size: 12.3px; line-height: 21.5px; text-align: justify; }
  .btn-solid { background: var(--accent); color: var(--white); font-weight: 700; font-size: 11px; border-radius: 18px;
    text-align: center; letter-spacing: 0.5px; }

  /* Recipes */
  .tile { overflow: hidden; }
  .tile-label { position: absolute; background: var(--black); color: var(--white); font-size: 17px; padding: 0 14px;
    height: 44px; line-height: 44px; }
  .recipes-title { left: 537px; top: 1099px; width: 128px; height: 385px; background: var(--black); }
  .recipes-title span { position: absolute; left: 64px; top: 192px; transform: translate(-50%,-50%) rotate(90deg);
    color: var(--white); font-size: 44px; letter-spacing: 10px; white-space: nowrap; }
  .tile-hover { position: absolute; left: 0; top: 60px; width: 100%; text-align: center; color: var(--white);
    font-size: 11px; font-weight: 600; }

  /* Nutrition */
  .nutrition-photo { left: 520px; top: 1484px; width: 680px; height: 261px;
    background: linear-gradient(100deg, #dfe2dd 0%, #c4cbb6 35%, #8fa65a 55%, #d79a2a 75%, #c7301e 100%); }
  .nutrition-dark { left: 0; top: 1484px; }
  .nutrition-title { left: 249px; top: 1560px; font-size: 34px; color: var(--accent); }
  .nutrition-sub { left: 249px; top: 1604px; font-size: 15px; color: var(--white); }

  /* Contact */
  .contact-title { left: 0; top: 1795px; width: 1200px; text-align: center; font-size: 34px; }
  .map { left: 0; top: 1858px; width: 605px; height: 490px; background: linear-gradient(135deg, #e6e6e6, #d9d9d9 60%, #e4e4e4); }
  .address-card { left: 166px; top: 1951px; width: 204px; height: 99px; background: var(--white); font-size: 10.5px;
    line-height: 26px; padding: 6px 0 0 44px; box-shadow: 0 1px 3px rgba(0,0,0,0.15); }
  .address-card svg { position: absolute; left: 20px; top: 13px; }
  .cta-title { left: 648px; top: 1884px; font-size: 18px; line-height: 25px; color: var(--accent); }
  .hours-title { left: 648px; top: 1944px; font-size: 15px; color: var(--accent); }
  .hours { left: 648px; top: 1976px; font-size: 16px; line-height: 21px; color: var(--grey-text); }
  .field { left: 648px; width: 358px; border: 1px solid var(--line); font-size: 10.5px; color: #555; padding: 13px 0 0 21px; }

  /* Contact band */
  .contact-band { left: 0; top: 2352px; width: 1200px; height: 113px;
    background: linear-gradient(90deg, #2a2524, #1a1616 50%, #2b2726); }
  .band-icon { width: 40px; height: 40px; border-radius: 50%; background: var(--white); }
  .band-icon svg { position: absolute; left: 10px; top: 10px; }
  .band-label { color: var(--white); font-size: 17px; }
  .band-value { color: var(--white); font-size: 25px; }

  /* Footer */
  .footer-links { left: 202px; top: 2496px; font-size: 13px; color: #333; }
  .footer-links b { font-weight: 400; margin: 0 9px; }
  .social { top: 2488px; width: 26px; height: 26px; background: #f0f0f0; }
  .social.active { background: #1565c0; }
  .copyright { left: 771px; top: 2528px; font-size: 9.5px; color: #333; }
</style>
</head>
<body>

<!-- Hero -->
<section class="abs hero" role="img" aria-label="Smiling chef in white uniform working in a bright kitchen with fresh tomatoes"></section>
<div class="abs menu-toggle"><span></span><span></span><span></span></div>
<div class="abs slide-arrow" style="left:161px"><svg width="12" height="16" viewBox="0 0 12 16"><path d="M9 1 L3 8 L9 15" stroke="#fff" stroke-width="2" fill="none"/></svg></div>
<div class="abs slide-arrow" style="left:991px"><svg width="12" height="16" viewBox="0 0 12 16"><path d="M3 1 L9 8 L3 15" stroke="#fff" stroke-width="2" fill="none"/></svg></div>
<div class="abs brand serif">LEO</div>
<div class="abs brand-sub serif">CHEF</div>
<p class="abs hero-copy serif">I work as a private chef for last 10 years, traveling all around the world<br>and cooking in private megayacht and villas.</p>
<a class="abs btn-outline">MY STORY</a>

<!-- Navigation -->
<nav class="serif">
  <span class="abs main-nav" style="left:390px">Home</span>
  <span class="abs main-nav" style="left:505px">About Us</span>
  <span class="abs main-nav" style="left:648px">Menus</span>
  <span class="abs main-nav" style="left:768px">Contact</span>
</nav>
<div class="abs nav-active-line"></div>

<!-- Intro -->
<div class="abs intro-frame"></div>
<div class="abs intro-photo" role="img" aria-label="Chef garnishing plated dishes with herbs"></div>
<h2 class="abs intro-title serif" style="font-weight:400">Personal Chef Menu</h2>
<p class="abs intro-text">This menu is just a sample of what I have to offer. They all can be modified and adjusted to suit your budget, tastes, dietary needs, and allergies. When we meet for our initial visit we will discuss any special request and we will chose a perfect menu for you and your families tastes. All entrees come with one side item, vegetable or starch . We will discuss what sides best accompany each dish considering your diet.</p>
<a class="abs btn-solid" style="left:596px;top:945px;width:107px;height:35px;line-height:35px">READ MORE</a>

<!-- Recipes -->
<div class="abs tile" style="left:0;top:1099px;width:291px;height:385px;background:linear-gradient(150deg,#7fa05a,#d8703f 40%,#b8552d 70%,#e9e2d8)" role="img" aria-label="Grilled salmon steak with salad">
  <span class="tile-label serif" style="left:0;top:0">Seafood</span></div>
<div class="abs tile" style="left:291px;top:1099px;width:246px;height:192px;background:linear-gradient(135deg,#e8531c,#d9420f 50%,#f06a2a)" role="img" aria-label="Spicy chicken pieces">
  <div class="tile-hover"><div style="font-size:22px;font-weight:400;line-height:22px">+</div>READ MORE</div>
  <span class="tile-label serif" style="left:0;bottom:0">Chicken</span></div>
<div class="abs tile" style="left:291px;top:1291px;width:246px;height:193px;background:linear-gradient(135deg,#f4f4ef,#7fae4a 45%,#d8412a 75%,#f2f2ee)" role="img" aria-label="Fresh entree salad with cucumber and tomato">
  <span class="tile-label serif" style="right:0;bottom:0">Entree Salads</span></div>
<div class="abs recipes-title"><span class="serif">Recipes</span></div>
<div class="abs tile" style="left:665px;top:1099px;width:245px;height:192px;background:linear-gradient(150deg,#3a2b24,#8b4a2e 45%,#c33a22 75%,#3b2d25)" role="img" aria-label="Grilled beef steaks with tomatoes">
  <span class="tile-label serif" style="left:0;top:0">Beef</span></div>
<div class="abs tile" style="left:665px;top:1291px;width:245px;height:193px;background:linear-gradient(150deg,#5a3a26,#d98a3e 45%,#e7b86a 65%,#4a2f20)" role="img" aria-label="Bowl of soup with beans">
  <span class="tile-label serif" style="right:0;bottom:0">Soups</span></div>
<div class="abs tile" style="left:910px;top:1099px;width:290px;height:385px;background:linear-gradient(150deg,#d6c8b3,#f08a2a 30%,#5e9a36 60%,#c43423 85%,#efe8dc)" role="img" aria-label="Vegetables on a cutting board">
  <span class="tile-label serif" style="left:0;top:0">Vegetarian</span></div>

<!-- Nutrition -->
<div class="abs nutrition-photo" role="img" aria-label="Fresh vegetables and herbs"></div>
<svg class="abs nutrition-dark" width="670" height="261" viewBox="0 0 670 261"><polygon points="0,0 665,0 528,261 0,261" fill="#0b0b0b"/></svg>
<h2 class="abs nutrition-title serif" style="font-weight:400">Nutritional advices</h2>
<p class="abs nutrition-sub">A Personal and Private Chef services.</p>
<a class="abs btn-solid" style="left:245px;top:1651px;width:106px;height:32px;line-height:32px">READ MORE</a>

<!-- Contact -->
<h2 class="abs contact-title serif" style="font-weight:400">Contact Us</h2>
<div class="abs map" role="img" aria-label="Street map of the city showing the studio location"></div>
<div class="abs address-card">
  <svg width="10" height="14" viewBox="0 0 10 14"><path d="M5 0C2.2 0 0 2.2 0 5c0 3.8 5 9 5 9s5-5.2 5-9C10 2.2 7.8 0 5 0zm0 7a2 2 0 1 1 0-4 2 2 0 0 1 0 4z" fill="#222"/></svg>
  Address : Leo Chef Kitchen<br>Level 12, 8 Harbour Lane<br>Bayside 2100
</div>
<p class="abs cta-title">CONTACT US TODAY TO SCHEDULE<br>A FREE CONSULTATION.</p>
<p class="abs hours-title">Opening Hours</p>
<p class="abs hours">Mon to Sat&nbsp; : &nbsp;9.00 am to 8.00 pm<br>Sunday Holiday</p>
<form>
  <div class="abs field" style="top:2045px;height:41px">Name</div>
  <div class="abs field" style="top:2098px;height:41px">Email</div>
  <div class="abs field" style="top:2151px;height:42px">Phone Number</div>
  <div class="abs field" style="top:2206px;height:72px">Message</div>
  <a class="abs btn-solid" style="left:648px;top:2297px;width:106px;height:34px;line-height:34px">SUBMIT</a>
</form>

<!-- Contact band -->
<div class="abs contact-band" role="img" aria-label="Harbour at dusk"></div>
<div class="abs band-icon" style="left:203px;top:2390px"><svg width="20" height="20" viewBox="0 0 24 24"><path d="M6.6 10.8a15.1 15.1 0 0 0 6.6 6.6l2.2-2.2a1 1 0 0 1 1-.25 11.4 11.4 0 0 0 3.6.57 1 1 0 0 1 1 1V20a1 1 0 0 1-1 1A17 17 0 0 1 3 4a1 1 0 0 1 1-1h3.5a1 1 0 0 1 1 1c0 1.25.2 2.45.57 3.57a1 1 0 0 1-.25 1z" fill="#f4460f"/></svg></div>
<span class="abs band-label serif" style="left:262px;top:2382px">Call Us</span>
<span class="abs band-value" style="left:262px;top:2402px">1-800 555 0142</span>
<div class="abs band-icon" style="left:631px;top:2390px"><svg width="20" height="20" viewBox="0 0 24 24"><rect x="2" y="5" width="20" height="14" rx="2" fill="none" stroke="#f4460f" stroke-width="2"/><path d="M3 6l9 7 9-7" fill="none" stroke="#f4460f" stroke-width="2"/></svg></div>
<span class="abs band-label serif" style="left:691px;top:2382px">Email</span>
<span class="abs band-value" style="left:691px;top:2402px">hello@leochef.com</span>

<!-- Footer -->
<nav class="abs footer-links serif">Home<b>::</b>About Us<b>::</b>Menus<b>::</b>Contact Us</nav>
<div class="abs social active" style="left:874px"></div>
<div class="abs social" style="left:908px"></div>
<div class="abs social" style="left:942px"></div>
<div class="abs social" style="left:976px"></div>
<p class="abs copyright">© 2016 .www.leochef.com&nbsp; | &nbsp;All Rights Reserved.</p>

</body>
</html>
```